Snapnook needs You

Help us create an inviting, amazing, sleek, simple, clear landing page for a picture-memory-social connection site!

Business Name: SnapNook
Industry: Social Networking and Creativity through Pictures
A web platform for and about a community that is driven by a passion for sharing, caring, bonding, collaborating, creating and earning with pictures, through pictures and other related creative activities. This is going to be a great site for all creative artists-photographers, artists, graphic artists to express their work and their creativity.

The main focus of the site is - CONNECTIONS.
This will be uncoded.

Desired Website Screen Size
1024x768... Widescreen/Landscape orientation, is what we mean... So it fits on a CPU screen.

Desired look and feel and message
Look: Visitor should feel immersed in the page, in the world the page creates, simple, elegant, sophisticated, contemporary. We really like a clean uncluttered look.

Special mention: By the way we love the marketing genius who thought up this branding for velu yogurt where they used the two dots above the o to create a branding effect that made this brand instantly identifiable. http://www.velu-dairy.ca/en/

The two dots by themselves without having even the name present brings up the whole brand now. The dots are used above all the ingredients of the yogurt creating friendly figures, and above people in commercials-bringing the people onto the side of "team" velu. Snapnook may have a character created or something distinctive in the letters in the name created to brand the site as well.

Feel: Engaging; Magical without being corny, here is a link to give an example look and feel but please do not be hindered in your creativity by this suggestion. We love all creative angles.
http://artscrapyard.com/graphic/5829317-camera-film-roll-blue-background

Message: Life and memories and connections through pictures.

Target audience:
The site is focused on pictures but not confined to photography enthusiasts (although they are an integral part of the site). Customers/Visitors will include families, corporates and the younger generation - all age groups, all class, everyone with pictures to express, memories to share.

Website design we like:
http://brindlework.com/work/northern-ballet-house/
http://brindlework.com/work/zapverse/

What colors do we want to see on our landing page?
We would like the background to be grey or blue since it is grey is picture neutral colour and blue highlights pictures well and we also like blue and silver, which can be integrated into the theme. Also like green. But please do not let these instructions limit your creativity. We are open to new ideas and colours.

Predetermined Concepts if any:
We have a concept in mind and we think it would be cool to have an interface for the user through the back of a camera on the landing page -This could be used to create a scene or world the visitor feels a part of or is immersed into. The back screen of the camera may act as a screen for the slideshow of featured pictures on the site.

Content on the Page:
Photo Gallery with full screen, thumbnail view, zoom option etc.
Prominent but short introductory message
Sign in / Login Options
Links: Home Page; About; Info/Help; Contact Us; Privacy Policy; Terms of Use
At the bottom of the page: Follow Me/Like/Workplaza...social buttons.

Please feel free to add any other element to the landing page that you think might add to the effect of simple yet amazing look -clean, simple, uncluttered, sophisticated, stylish, inviting and engaging.
The concept is a guideline, but we would like you to be as creative as you can, even if it meant stepping out of these guidelines - rethink design, style, content if you like. We believe in bringing a solution in an innovative yet simple and elegant style. Something a visitor would be intrigued enough to explore and the guest would feel comfortable enough taking that step forward to have fun on the site. If you believe in the same, and you have the skill then you will have what we need. Good luck, go for it and we are excited to see what the amazing designers on this amazing site have to offer.
If you have any questions please free to ask.

HI wanted to send an update that this project design has been guaranteed.

Our site will be one to celebrate and showcase imagination as well as connection.  We would love to see what you create. Keep in mind our site will showcase all creativity, photographs, artists, graphic artists so this would be a benefit you may want to take advantage of in the future, a place where, if you so choose, you could gain exposure for your work. Therefore, even if you do not win the design project there is possible future benefit.

Imagination is everything.
Imagination encircles the world.-Halvorsen

Reason: We are giving the designers who accepted invites but have not yet submitted a chance to finish their submissions and the ones who are working on revisions a chance to finish those:)

Hello everyone,

Due to time constraints we must come to a decision sooner than the deadline of 28th. 

So, please try to submit any new designs or modifications to the old ones before the 26th. We are very thankful to all of you who have participated - for your designs, enthusiasm and kind words. 

Good luck! :)

• Thank you for the interest shown and your submissions! Designers who have submitted up until now have shown great potential. We are VERY excited with the quality of work and designs.

We want to add that Snapnook is not exclusively for the photographers. The site is for every person who may have a picture to store, organise, use or share - whether publicly or with only a few friends and family.

Snapnook is about allowing people to take control of their creativity. It is about providing tools to our users so that they can build their own connections and social network... of friends, family, fans, clients, ideas, thoughts, emotions etc. through pictures without worrying about their privacy or control over their creations.

With this update we want to encourage others to go beyond the camera theme. Do not let us restrict your creativity. Let YOUR OWN ideas take over if that’s what you think will best convey the message and will appeal to the users.

```html
<!DOCTYPE html>
<html lang="en">
<head>
<meta charset="utf-8">
<title>SnapNook – Landing</title>
<link rel="stylesheet" href="https://fonts.googleapis.com/css2?family=Arimo:ital,wght@0,400;0,700;1,400;1,700&display=swap">
<style>
  :root {
    --hero-top: #8e8e8e;
    --hero-mid: #5a5a5a;
    --hero-bottom: #050505;
    --photo-light: rgba(205,205,205,0.55);
    --photo-mid: rgba(140,140,140,0.45);
    --photo-shade: rgba(40,40,40,0.5);
    --band-white: #ffffff;
    --band-fade: #d8d8d8;
    --band-shadow: rgba(120,120,120,0.35);
    --nav-blue: #12c9f2;
    --nav-tab: #0fb4dc;
    --nav-tab-dark: #0a9fc5;
    --nav-marker: #4a4a4a;
    --footer-bg: #3b3b3d;
    --footer-light: #5a5a5c;
    --accent-orange: #f08a12;
    --accent-orange-light: #ffa735;
    --accent-orange-dark: #c96a05;
    --text-white: #ffffff;
    --text-soft: #e6e6e6;
    --text-grey: #6a6a6a;
    --text-footer: #b9b9b9;
    --field-grey: #7c7c7c;
    --icon-blue: #1a9ed8;
    --icon-blue-light: #6fd3ff;
    --social-1: #3b5a9a;
    --social-2: #c23a2c;
    --social-3: #f07a1a;
    --social-4: #2fae2f;
  }
  * { margin: 0; padding: 0; box-sizing: border-box; }
  html, body { width: 1200px; height: 739px; overflow: hidden; }
  body { font-family: "Arimo", Arial, sans-serif; background: var(--footer-bg); }

  .page { position: relative; width: 1200px; height: 739px; overflow: hidden; }

  .hero {
    position: absolute; left: 0; top: 0; width: 1200px; height: 484px;
    background: linear-gradient(180deg, var(--hero-top) 0%, var(--hero-mid) 45%, var(--hero-bottom) 100%);
  }
  .hero-photo {
    position: absolute; left: 0; top: 0; width: 1200px; height: 540px;
    background:
      radial-gradient(ellipse 170px 230px at 385px 300px, var(--photo-shade), transparent 72%),
      radial-gradient(ellipse 250px 300px at 390px 300px, var(--photo-mid), transparent 70%),
      radial-gradient(ellipse 130px 200px at 520px 230px, var(--photo-light), transparent 70%),
      radial-gradient(ellipse 300px 170px at 730px 330px, var(--photo-mid), transparent 72%),
      radial-gradient(ellipse 260px 120px at 1000px 30px, var(--photo-light), transparent 70%);
  }

  .brand { position: absolute; left: 213px; top: 58px; display: flex; align-items: baseline; gap: 10px; }
  .brand-name { font-size: 29px; font-weight: 400; color: var(--text-white); letter-spacing: 0.3px; }
  .brand-tagline { font-size: 12px; font-weight: 700; font-style: italic; color: var(--text-white); }

  .social { position: absolute; left: 711px; top: 62px; display: flex; gap: 3px; }
  .social span { width: 15px; height: 14px; border-radius: 2px; display: block; }
  .social .s1 { background: var(--social-1); }
  .social .s2 { background: var(--social-2); }
  .social .s3 { background: var(--social-3); }
  .social .s4 { background: var(--social-4); }

  .search-icon { position: absolute; left: 792px; top: 60px; }
  .search-field {
    position: absolute; left: 819px; top: 58px; width: 183px; height: 22px;
    border-radius: 4px; background: var(--field-grey);
    box-shadow: inset 0 1px 2px rgba(0,0,0,0.35);
    font-size: 13px; font-style: italic; color: var(--text-soft);
    padding: 3px 8px;
  }

  .signup-btn {
    position: absolute; left: 567px; top: 261px; width: 81px; height: 22px;
    border-radius: 3px;
    background: linear-gradient(180deg, var(--accent-orange-light), var(--accent-orange) 55%, var(--accent-orange-dark));
    color: var(--text-white); font-size: 13px; font-style: italic;
    text-align: center; line-height: 22px;
  }
  .intro {
    position: absolute; left: 340px; top: 301px; width: 532px;
    text-align: center; color: var(--text-white);
    font-size: 11.4px; font-style: italic; line-height: 12.6px;
  }
  .free-trial {
    position: absolute; left: 500px; top: 347px; width: 220px; text-align: center;
    color: var(--text-white); font-size: 14.5px; font-style: italic; letter-spacing: 0.5px;
  }

  .features {
    position: absolute; left: 0; top: 484px; width: 1200px; height: 103px;
    background:
      radial-gradient(ellipse 160px 60px at 390px 0, var(--band-shadow), transparent 75%),
      radial-gradient(ellipse 200px 50px at 700px 0, var(--band-shadow), transparent 75%),
      linear-gradient(180deg, var(--band-white) 0%, var(--band-white) 55%, var(--band-fade) 100%);
  }
  .feature { position: absolute; top: 42px; display: flex; gap: 5px; }
  .feature-one { left: 292px; }
  .feature-two { left: 628px; }
  .feature-go {
    width: 16px; height: 16px; border-radius: 50%; margin-top: 7px; flex: none;
    background: radial-gradient(circle at 40% 35%, var(--icon-blue-light), var(--icon-blue));
    color: var(--text-white); font-size: 6px; font-weight: 700; font-style: italic;
    text-align: center; line-height: 16px;
  }
  .feature p { font-size: 11.4px; font-style: italic; color: var(--text-grey); line-height: 12.6px; }

  .main-nav {
    position: absolute; left: 0; top: 587px; width: 1200px; height: 35px;
    background: var(--nav-blue);
  }
  .nav-tab {
    position: absolute; top: 0; height: 35px; z-index: 0; isolation: isolate;
    color: var(--text-white); font-size: 17px; text-align: center; line-height: 34px;
  }
  .nav-tab::before {
    content: ""; position: absolute; inset: 0; z-index: -1;
    background: linear-gradient(90deg, var(--nav-tab-dark), var(--nav-tab) 30%, var(--nav-blue));
    transform: skewX(-14deg);
  }
  .tab-home { left: 208px; width: 88px; }
  .tab-products { left: 302px; width: 90px; }
  .tab-about { left: 396px; width: 82px; }
  .tab-contact { left: 482px; width: 88px; }
  .nav-marker {
    position: absolute; left: 333px; top: 33px; width: 16px; height: 8px;
    border-radius: 0 0 8px 8px; background: var(--nav-marker);
  }
  .signin-label {
    position: absolute; left: 745px; top: 7px;
    font-size: 16px; font-style: italic; color: var(--text-white);
  }
  .signin-field {
    position: absolute; left: 826px; top: 6px; width: 146px; height: 23px;
    border-radius: 3px; background: var(--nav-tab-dark);
    box-shadow: inset 0 1px 2px rgba(0,0,0,0.3);
    font-size: 14px; font-style: italic; color: var(--text-white); padding: 3px 8px;
  }
  .signin-go {
    position: absolute; left: 982px; top: 7px; font-size: 15px; font-style: italic; color: var(--text-white);
  }

  .site-footer {
    position: absolute; left: 0; top: 622px; width: 1200px; height: 117px;
    background:
      radial-gradient(ellipse 380px 120px at 600px 0, var(--footer-light), transparent 75%),
      var(--footer-bg);
  }
  .footer-note {
    position: absolute; left: 450px; top: 47px; width: 300px; text-align: center;
    font-size: 10.5px; font-style: italic; color: var(--text-footer); line-height: 12px;
  }
  .footer-line {
    position: absolute; left: 0; top: 78px; width: 1200px;
    display: flex; justify-content: center; align-items: center; gap: 9px;
    font-size: 9.8px; font-style: italic; color: var(--text-footer);
  }
  .footer-brand { font-size: 15px; font-style: normal; color: var(--text-white); }
</style>
</head>
<body>
<div class="page">
  <section class="hero">
    <div class="hero-photo" role="img" aria-label="Moody grey photograph of large three-dimensional letters spelling the word connection"></div>
  </section>

  <header>
    <div class="brand">
      <span class="brand-name">SNAPNOOK</span>
      <span class="brand-tagline">PROFESSIONAL PHOTO</span>
    </div>
    <div class="social" aria-label="Social links">
      <span class="s1"></span><span class="s2"></span><span class="s3"></span><span class="s4"></span>
    </div>
    <svg class="search-icon" width="22" height="22" viewBox="0 0 22 22" aria-hidden="true">
      <circle cx="14" cy="8" r="4.5" fill="none" stroke="#1aa5e6" stroke-width="2.4"/>
      <line x1="10.8" y1="11.2" x2="4" y2="18" stroke="#1aa5e6" stroke-width="3" stroke-linecap="round"/>
    </svg>
    <div class="search-field">Search</div>
  </header>

  <div class="signup-btn">SIGN UP</div>
  <p class="intro">Te dicam labitur mel, est eu graeco minimum, in sit facer assueverit inciderint.<br>
    Laudem diceret no his, et mea minim nominati democritum, at quo partem<br>
    numquam feugiat. Liber primis maiestatis ius ut. Ius liber congue laboramus ne.</p>
  <div class="free-trial">FREE&nbsp; TRIAL</div>

  <section class="features">
    <div class="feature feature-one">
      <span class="feature-go">GO</span>
      <p>Te dicam labitur mel, est eu graeco minimum,<br>in sit facer assueverit inciderint. Laudem diceret no</p>
    </div>
    <div class="feature feature-two">
      <span class="feature-go">GO</span>
      <p>Te dicam labitur mel, est eu graeco minimum,<br>in sit facer assueverit inciderint. Laudem diceret no</p>
    </div>
  </section>

  <nav class="main-nav">
    <span class="nav-tab tab-home">home</span>
    <span class="nav-tab tab-products">products</span>
    <span class="nav-tab tab-about">about</span>
    <span class="nav-tab tab-contact">contact</span>
    <span class="nav-marker"></span>
    <span class="signin-label">SIGN IN</span>
    <div class="signin-field">email</div>
    <span class="signin-go">GO</span>
  </nav>

  <footer class="site-footer">
    <p class="footer-note">Te dicam labitur mel, est eu graeco<br>minimum, in sit facer assueverit inciderint.</p>
    <div class="footer-line">
      <span>minimum, in sit facer assueverit inciderint.</span>
      <span class="footer-brand">SNAPNOOK</span>
      <span>minimum, in sit facer assueverit inciderint.</span>
    </div>
  </footer>
</div>
</body>
</html>
```